Profesional personal website needs design and business card

I need a business card with my professional name as a logo "Dorian Vitality" for my business. I am a Wellness Coach, consultant and trainer. So it should be professional, wellness oriented and modern.

Target Market(s)

Private clients, governments, corporations. Luxury and high market.

Industry/Entity Type

Health And Wellness

Contact Information for Business Card

Dorian Vitality should be the logo

Colors

Designer to choose colors to be used in the design.

Requirements
Must have
• Dorian Vitality
• Name: Tomás Lirandel
• Wellness Coach, Consultant & Trainer.
• Website: www.dorianvitality-example.com
• Phone:
• Spain (+34) 612 480 317
• (USA) +1 (555) 610 4829
Nice to have
• The most important is the design of "Dorian Vitality", as this is going to be my personal brand logo. It should be professional, wellness, high end and actual.
Should not have
• no golds, no baroque style..

```html
<!DOCTYPE html>
<html lang="en">
<head>
<meta charset="UTF-8">
<title>Dorian Vitality — Business Card</title>
<link href="https://fonts.googleapis.com/css2?family=Arimo:wght@400;700&display=swap" rel="stylesheet">
<style>
  :root {
    --backdrop: #e9eae7;
    --card-dark: #3c3c3c;
    --card-light: #ffffff;
    --brand-green: #6bb41c;
    --ink: #3a3a3a;
    --ink-soft: #4a4a4a;
  }
  * { margin: 0; padding: 0; box-sizing: border-box; }
  html, body {
    width: 1200px; height: 1200px; overflow: hidden;
    background: var(--backdrop);
    font-family: "Arimo", Arial, sans-serif;
  }
  .canvas {
    position: relative; width: 1200px; height: 1200px;
  }
  .card {
    position: absolute; left: 180px; width: 840px; height: 480px;
    box-shadow: 0 6px 18px rgba(0,0,0,0.18);
  }
  .card-back {
    top: 90px;
    background: var(--card-dark);
    border-radius: 70px 0 70px 0;
    display: flex; align-items: center; justify-content: center;
  }
  .brand-mark {
    display: flex; align-items: center; gap: 18px;
  }
  .brand-dot {
    width: 46px; height: 46px; border-radius: 50%;
    background: var(--brand-green);
  }
  .brand-name {
    font-weight: 700; font-size: 46px; letter-spacing: -0.5px;
  }
  .card-back .brand-name { color: var(--brand-green); }

  .card-front {
    top: 630px;
    background: var(--card-light);
    border-radius: 0 70px 0 70px;
  }
  .front-brand {
    position: absolute; right: 70px; top: 70px;
    display: flex; flex-direction: column; align-items: center; gap: 22px;
  }
  .front-brand .brand-dot { width: 110px; height: 110px; background: var(--brand-green); }
  .front-brand .brand-name { color: var(--ink); font-size: 44px; }

  .contact-block {
    position: absolute; left: 60px; bottom: 62px;
  }
  .person-name {
    color: var(--brand-green); font-weight: 700; font-size: 34px;
    margin-bottom: 6px;
  }
  .person-role {
    color: var(--ink-soft); font-size: 22px; margin-bottom: 20px;
  }
  .contact-line {
    display: flex; align-items: center; gap: 8px;
    color: var(--ink-soft); font-size: 22px; line-height: 1.35;
  }
  .contact-line .region { color: var(--brand-green); }
  .contact-icon { width: 22px; height: 22px; flex: none; }
</style>
</head>
<body>
<div class="canvas">
  <section class="card card-back" aria-label="Card back">
    <div class="brand-mark">
      <span class="brand-dot"></span>
      <span class="brand-name">Dorian Vitality</span>
    </div>
  </section>

  <section class="card card-front" aria-label="Card front">
    <div class="front-brand">
      <span class="brand-dot"></span>
      <span class="brand-name">Dorian Vitality</span>
    </div>

    <div class="contact-block">
      <p class="person-name">Tomás Lirandel</p>
      <p class="person-role">Wellness Coach, Consultant &amp; Trainer</p>
      <p class="contact-line">
        <svg class="contact-icon" viewBox="0 0 24 24" aria-hidden="true">
          <circle cx="12" cy="12" r="10.5" fill="none" stroke="#6bb41c" stroke-width="2"/>
          <path d="M9 6.5c-1 .4-1.8 1.4-1.6 2.8.4 3 3.3 6.3 6.3 7.2 1.3.4 2.4-.3 2.9-1.2l-2-1.6-1.2.8c-1.2-.6-2.4-1.9-3-3.1l.9-1.1z" fill="#6bb41c"/>
        </svg>
        <span>(+34) 612 480 317 <span class="region">(SPAIN)</span></span>
      </p>
      <p class="contact-line">
        <svg class="contact-icon" viewBox="0 0 24 24" aria-hidden="true">
          <circle cx="12" cy="12" r="10.5" fill="none" stroke="#6bb41c" stroke-width="2"/>
          <path d="M9 6.5c-1 .4-1.8 1.4-1.6 2.8.4 3 3.3 6.3 6.3 7.2 1.3.4 2.4-.3 2.9-1.2l-2-1.6-1.2.8c-1.2-.6-2.4-1.9-3-3.1l.9-1.1z" fill="#6bb41c"/>
        </svg>
        <span>+1 (555) 610 4829<span class="region">(USA)</span></span>
      </p>
      <p class="contact-line">
        <svg class="contact-icon" viewBox="0 0 24 24" aria-hidden="true">
          <g fill="none" stroke="#6bb41c" stroke-width="2">
            <circle cx="12" cy="12" r="10"/>
            <ellipse cx="12" cy="12" rx="4.5" ry="10"/>
            <line x1="2" y1="12" x2="22" y2="12"/>
            <path d="M4 7h16M4 17h16"/>
          </g>
        </svg>
        <span>www.dorianvitality-example.com</span>
      </p>
    </div>
  </section>
</div>
</body>
</html>
```